New Business Card Design Project

Need a design that will create an impact / strong impression towards our clients for our business. We are in the lighting business and we do lighting retrofits for large commercial to industrial clientele.

Target Market(s)

Lighting Industry

Industry/Entity Type

Business

Font styles to use
Other font styles liked:
• we would like to use the font on our logo, not sure what it is though..

Requirements
Must have
• Our logo.
Nice to have
• We are open to suggestions that have to do with lighting.

```html
<!DOCTYPE html>
<html lang="en">
<head>
<meta charset="utf-8">
<title>Voltwise Retrofit Group – Business Card</title>
<link rel="stylesheet" href="https://fonts.googleapis.com/css2?family=Roboto+Condensed:wght@400;700&display=swap">
<style>
  :root {
    --bg: #e9e7e2;
    --card-white: #f7f7f5;
    --forest: #1d4d1f;
    --leaf: #3c9a3f;
    --lime: #6cc655;
    --ink-light: #ffffff;
    --ink-soft: #dfe9dc;
    --shadow: rgba(0,0,0,0.18);
  }
  * { margin: 0; padding: 0; box-sizing: border-box; }
  html, body { width: 1200px; height: 911px; overflow: hidden; }
  body {
    background: var(--bg);
    font-family: "Roboto Condensed", "Arial Narrow", sans-serif;
    position: relative;
  }
  .card {
    position: absolute;
    width: 600px;
    height: 343px;
    border-radius: 18px;
    background: var(--card-white);
    box-shadow: 0 10px 28px var(--shadow);
    overflow: hidden;
  }
  .card--front { left: 60px; top: 110px; }
  .card--back { left: 540px; top: 470px; }

  .front-panel { position: absolute; inset: 0; }

  .brand {
    position: absolute;
    color: var(--forest);
    font-weight: 700;
    text-transform: uppercase;
    line-height: 1;
    white-space: nowrap;
  }
  .card--front .brand { left: 48px; top: 100px; font-size: 30px; letter-spacing: 0.3px; }
  .card--back .brand { right: 50px; top: 60px; font-size: 52px; text-align: right; }

  .identity {
    position: absolute;
    left: 330px;
    top: 196px;
    width: 150px;
    color: var(--ink-light);
    white-space: nowrap;
  }
  .person-name { font-size: 20px; font-weight: 700; letter-spacing: 0.5px; }
  .person-title { font-size: 14px; color: var(--ink-soft); margin-top: 2px; }
  .address { font-size: 13px; color: var(--ink-soft); margin-top: 18px; line-height: 1.4; }

  .divider {
    position: absolute;
    left: 490px;
    top: 180px;
    width: 1px;
    height: 135px;
    background: rgba(255,255,255,0.35);
  }

  .contacts {
    position: absolute;
    left: 392px;
    top: 30px;
    list-style: none;
    color: var(--ink-light);
    font-size: 13px;
    white-space: nowrap;
  }
  .contacts li { display: flex; align-items: center; gap: 8px; height: 21px; }
  .contacts svg { width: 12px; height: 12px; flex: none; }

  .back-rule {
    position: absolute;
    right: 50px;
    top: 172px;
    width: 300px;
    height: 2px;
    background: var(--leaf);
  }
  .back-url {
    position: absolute;
    right: 50px;
    top: 184px;
    color: var(--forest);
    font-size: 15px;
  }
</style>
</head>
<body>

<section class="card card--front" aria-label="Business card front">
  <svg class="front-panel" viewBox="0 0 600 343" width="600" height="343" aria-hidden="true">
    <polygon points="372,0 600,0 600,343 312,343 312,150 372,138" fill="var(--forest)"/>
    <polygon points="300,343 312,343 312,150 300,153" fill="var(--lime)"/>
    <polygon points="312,150 372,138 372,132 312,144" fill="var(--leaf)"/>
  </svg>

  <div class="brand">Voltwise<br>Retrofit Group</div>

  <div class="identity">
    <div class="person-name">DANIEL REYES</div>
    <div class="person-title">CEO/FOUNDER</div>
    <div class="address">2140 Alder Ridge Road<br>Fairview, Oregon 97024</div>
  </div>

  <div class="divider"></div>

  <ul class="contacts">
    <li><svg viewBox="0 0 12 12"><path d="M3 1l2 2-1 1.5c.7 1.5 1.9 2.7 3.5 3.5L9 7l2 2-1.5 2C5 10.5 1.5 7 1 2.5z" fill="#fff"/></svg>555 214 0387</li>
    <li><svg viewBox="0 0 12 12"><rect x="3" y="0.5" width="6" height="11" rx="1" fill="none" stroke="#fff"/></svg>555 302 7716</li>
    <li><svg viewBox="0 0 12 12"><rect x="1" y="4" width="10" height="6" fill="#fff"/><rect x="3" y="1" width="6" height="3" fill="none" stroke="#fff"/></svg>555 419 2265</li>
    <li><svg viewBox="0 0 12 12"><rect x="0.5" y="2.5" width="11" height="7" fill="#fff"/><path d="M1 3l5 4 5-4" fill="none" stroke="var(--forest)"/></svg>daniel@voltwisegroup.com</li>
    <li><svg viewBox="0 0 12 12"><circle cx="6" cy="6" r="5.5" fill="#fff"/><path d="M1 6h10M6 1c-2 3-2 7 0 10M6 1c2 3 2 7 0 10" fill="none" stroke="var(--forest)" stroke-width="0.8"/></svg>www.voltwisegroup.com</li>
  </ul>
</section>

<section class="card card--back" aria-label="Business card back">
  <div class="brand">Voltwise<br>Retrofit Group</div>
  <div class="back-rule"></div>
  <div class="back-url">www.voltwiseretrofitgroup.com</div>
</section>

</body>
</html>
```